Calder Aviation website

We are an aviation company based in Miramar, FL but with worldwide coverage. We are involved in commercial aircraft (mostly freighters) trading, sale & leasing. Specifically, we specialized in freighters of the Veltram family (V316, V328, V335, V342, V359). We also assist with financing, sale/leaseback. Handle special aviation projects and provide consultancy services. Currently engaged in a Veltram 359 passenger to Freighter conversion (P2F).

Website Preliminary Initial Content/Sections as follows:

About Us
Founded in 2011, Calder Aviation's management has many years of experience in Aviation, a strong background in scheduled airlines with emphasis in all cargo operations, freight forwarding supply chain and freight logistics, as well as ACMI and CMI operations.

Calder’s focuses in facilitating wet and dry lease operations, charter and ACMI programs consultancy, aircraft sales, leasing and procurement, aviation consultancy and aircraft management.

Calder team is a hands-on reliable alternative that works toward achieving your aircraft and aviation objectives by meeting your requirements and timeframe throughout professional and personalized service.

Tiberio Salcedo has over three decades of experience in the aviation field including aircraft maintenance, airline management, supply chain and logistics management. Tiberio is a true entrepreneur with proven experience and expertise on the multiple facets of the commercial aviation industry throughout the creation and development of a cluster of aviation entities. Tiberio is the founder and former sole member/chairman of 64 Air, a Veltram 342 All-Cargo U.S. Certificated Air Carrier created from scratch in 2014 which nowadays conforms a superb growing airline platform with an immaculate compliance operational record.

Services

Aircraft Finance, Trading, Procurement and Leasing
Calder buys, sells, leases and facilitates aircraft trading while specializes in structured aircraft investment projects. Calder has deep industry relationships and years of expertise, allowing to successfully execute lease transactions. We assist airlines, financial institutions and leasing companies when selling or purchasing aircraft.

Aircraft Available for Sale/Lease

Sale/Leaseback
Sale-leaseback is a method of financing. If your company needs liquidity, your aircraft or engine can serve as collateral for a loan throughout a sale-leaseback transaction. Sale-leaseback can free the equity tied up in aircraft or asset. Even if there is no pressing need for funds, a sale-leaseback allows you to use the equity tied up in your aircraft in a more productive fashion. Leaseback arrangements are usually employed because they confer financing, accounting or taxation benefits.

Passenger to Freighter Conversion (P2F)
Pandemic has seen the resurgence of operators packing freight into the main cabins of passenger aircraft. Carriers have been allowed to transport cargo in the cabin by removing passenger seats completely. NAB/CARO have established exemptions that allow operators to fly in “Preighter” configuration for a limited time. Calder is closely working with a U.S. group that is developing a Class E Supplemental Type Certificate (STC) for applicability on V359 aircraft which will include a cargo door for containerized freight. Final approvals are expected during first quarter of 2022.
Wet lease
Throughout our deep relationships within the industry, Calder facilitates short or long-term wet leases to airlines and qualified parties around the globe, whereby we provide the Aircraft, Crews, Maintenance and Insurance (ACMI) worldwide services at competitive rates. We also specialize in AM leases where the aircraft is registered onto Lessee´s AOC with all maintenance services included in the rates, covering all maintenance risks, or CM or CMI where the client provides the aircraft.

Dry Lease
We offer aircraft from our own portfolio on dry lease or could engage in procuring the aircraft of your choice.

Asset & Aircraft Management
We provide aircraft owners Aircraft Management services, where we manage the technical side of the aircraft or the asset. Calder also provides Harlow Dynamics engines trading, repair and full management services. We also buy Veltram/Skylane surplus inventory.

Worldwide Charters
We facilitate the arrangement of full charters to airlines and logistics companies. Certain territory restrictions may apply.

Aviation Consultancy
We provide airline consultancy services for new or special projects. Calder also specializes on All Cargo International route analysis, implementation and development. Our team provides professional guidance in obtaining worldwide both scheduled and charter authority.

Target Market(s)

Our target market are the airlines, logistics companies and commercial aviation related entities

Industry/Entity Type

Commercial Aviation

Coding

Coded - Design and coding required

Number of Pages Required

3 page

Requirements
Must have
• Illustrations of wide body freighters such V359, V342, V328

```html
<!DOCTYPE html>
<html lang="en">
<head>
<meta charset="utf-8">
<title>Calder Aviation</title>
<link href="https://fonts.googleapis.com/css2?family=Questrial&family=Lato:wght@400;700&display=swap" rel="stylesheet">
<style>
:root{
  --navy:#0b1034;
  --navy-deep:#070a24;
  --navy-mid:#1a2358;
  --silver:#aab6c1;
  --ink:#1b1b1f;
  --text:#333;
  --white:#fff;
  --black:#000;
}
*{box-sizing:border-box;margin:0;padding:0}
html,body{width:1200px;height:4332px;overflow:hidden}
body{position:relative;background:var(--white);font-family:'Lato',sans-serif;color:var(--text)}
.abs{position:absolute}
h1,h2,h3,h4{font-family:'Questrial',sans-serif;font-weight:400}
.btn{position:absolute;display:flex;align-items:center;justify-content:center;border-radius:30px;font-family:'Questrial',sans-serif;font-size:17px;text-decoration:none}
.btn-light{background:var(--white);color:var(--ink)}
.btn-dark{background:var(--navy);color:var(--white)}

/* header */
.site-header{position:absolute;top:0;left:0;width:1200px;height:70px;background:var(--white);box-shadow:0 1px 4px rgba(0,0,0,.08);z-index:5}
.brand{position:absolute;left:118px;top:6px;width:176px;text-align:center;color:var(--navy);font-family:'Questrial',sans-serif}
.brand .name{font-size:30px;letter-spacing:1px;line-height:32px}
.brand .sub{font-size:12px;letter-spacing:12px;line-height:16px;padding-left:12px}
.nav a{position:absolute;top:25px;font-family:'Questrial',sans-serif;font-size:15px;color:var(--ink);text-decoration:none}
.login{left:975px;top:13px;width:114px;height:43px;font-size:17px}

/* hero */
.hero{position:absolute;top:70px;left:0;width:1200px;height:650px;
  background:linear-gradient(180deg,#25304f 0%,#3a4a6a 35%,#5a6072 55%,#2a2c35 75%,#141418 100%);
  clip-path:polygon(0 0,100% 0,100% 525px,50% 625px,0 525px)}
.hero-title{position:absolute;top:198px;width:1200px;text-align:center;color:var(--white);font-size:42px;letter-spacing:2px}
.hero-text{position:absolute;top:264px;width:1200px;text-align:center;color:#e8e8ee;font-size:15px;line-height:26px}

.section-title{position:absolute;width:1200px;text-align:center;color:var(--ink);font-size:36px;letter-spacing:1px}

/* services */
.arrow{position:absolute;top:1048px}
.service{position:absolute;top:882px;width:309px;height:358px;border-radius:10px;overflow:hidden;box-shadow:0 3px 8px rgba(0,0,0,.3);background:var(--navy)}
.service .photo{position:absolute;top:0;left:0;width:100%;height:299px}
.service .label{position:absolute;bottom:0;left:0;width:100%;height:59px;display:flex;align-items:center;justify-content:center;color:var(--white);font-family:'Questrial',sans-serif;font-size:22px}
.service.feature{background:linear-gradient(180deg,#1b2766,#0d1440)}
.feature h3{position:absolute;top:148px;width:100%;text-align:center;color:var(--white);font-size:20px;letter-spacing:.5px}
.feature p{position:absolute;top:190px;left:50px;right:50px;text-align:center;color:#e4e6f0;font-size:15px;line-height:26px}
.link{color:var(--white);font-size:15px;font-weight:700;text-decoration:underline}
.feature .link{position:absolute;top:308px;width:100%;text-align:center}

/* about */
.about{position:absolute;top:1320px;left:0;width:1200px;height:570px;
  background:linear-gradient(180deg,#1d2230 0%,#30333d 45%,#222430 100%);
  clip-path:polygon(0 7px,100% 138px,100% 453px,0 562px)}
.about h2{position:absolute;top:146px;width:100%;text-align:center;color:var(--white);font-size:36px}
.about p{position:absolute;top:206px;left:236px;width:728px;text-align:center;color:#f0f0f3;font-size:15px;line-height:26px}

.avail-text{position:absolute;top:2012px;left:208px;width:784px;text-align:center;color:var(--ink);font-size:15px;line-height:26px}

/* contact */
.contact{position:absolute;top:2263px;left:0;width:1200px;height:887px;
  background:linear-gradient(160deg,#222c66 0%,#152056 50%,#0f1848 100%);
  clip-path:polygon(0 131px,100% 0,100% 100%,0 781px)}
.contact h2{position:absolute;top:133px;width:100%;text-align:center;color:var(--white);font-size:36px}
.field-label{position:absolute;color:var(--white);font-family:'Questrial',sans-serif;font-size:19px;letter-spacing:.5px}
.field{position:absolute;background:var(--white);border-radius:30px;color:#999;font-size:14px;padding-left:24px;display:flex;align-items:center}
.field.area{border-radius:3px;align-items:flex-start;padding-top:18px}
.submit{left:536px;top:2975px;width:136px;height:54px}

/* focus */
.focus{position:absolute;width:474px;height:256px;border-radius:8px;overflow:hidden;background:var(--navy);box-shadow:0 2px 6px rgba(0,0,0,.25)}
.focus .photo{position:absolute;left:0;top:0;width:218px;height:100%}
.focus h3{position:absolute;left:238px;top:24px;right:8px;color:var(--white);font-size:23px;line-height:27px;letter-spacing:.3px}
.focus p{position:absolute;left:238px;right:20px;color:#e6e8f2;font-size:15px;line-height:26px}
.focus .link{position:absolute;left:238px}

/* footer */
.site-footer{position:absolute;top:3880px;left:0;width:1200px;height:452px;background:var(--black);
  clip-path:polygon(0 127px,50% 0,100% 127px,100% 100%,0 100%)}
.footer-brand{position:absolute;left:118px;top:4052px;width:230px;text-align:center;color:var(--white);font-family:'Questrial',sans-serif}
.footer-brand .name{font-size:38px;letter-spacing:2px;line-height:40px}
.footer-brand .sub{font-size:16px;letter-spacing:16px;line-height:24px;padding-left:16px}
.footer-col h4{position:absolute;top:4042px;color:var(--white);font-size:23px}
.footer-item{position:absolute;color:var(--white);font-size:15px;line-height:25px;display:flex;gap:10px;align-items:flex-start}
.footer-item svg{flex:none;margin-top:6px}
.social{position:absolute;top:4086px;left:936px;display:flex;gap:10px}
.social span{width:12px;height:12px;border-radius:50%;background:var(--white)}
.copyright{position:absolute;top:4264px;width:1200px;text-align:center;color:var(--white);font-size:15px}
</style>
</head>
<body>

<header class="site-header">
  <div class="brand"><div class="name">CALDER</div><div class="sub">AVIATION</div></div>
  <nav class="nav">
    <a style="left:377px" href="#">Home</a>
    <a style="left:458px" href="#">About Us</a>
    <a style="left:560px" href="#">Our Services</a>
    <a style="left:688px" href="#">Aircraft Available</a>
    <a style="left:847px" href="#">Contact Us</a>
  </nav>
  <a class="btn btn-dark login" href="#">Login</a>
</header>

<section class="hero" role="img" aria-label="Wide-body cargo freighter parked on an airport apron at dusk with ground equipment"></section>
<svg class="abs" style="left:0;top:590px" width="1200" height="140" viewBox="0 590 1200 140">
  <polygon points="18,606 600,716 1182,606 1168,598 600,693 32,598" fill="var(--silver)"/>
</svg>
<h1 class="hero-title">CALDER AVIATION</h1>
<p class="hero-text">Lorem ipsum dolor sit amet, consectetur adipiscing elit, sed do eiusmod<br>tempor incididunt ut labore et dolore magna aliqua.</p>
<a class="btn btn-light" style="left:517px;top:343px;width:166px;height:54px" href="#">Learn More</a>

<h2 class="section-title" style="top:795px">Our Services</h2>
<svg class="arrow" style="left:42px" width="16" height="24" viewBox="0 0 16 24"><path d="M12 4 L5 12 L12 20" fill="none" stroke="var(--ink)" stroke-width="3"/></svg>
<svg class="arrow" style="left:1136px" width="16" height="24" viewBox="0 0 16 24"><path d="M4 4 L11 12 L4 20" fill="none" stroke="var(--ink)" stroke-width="3"/></svg>

<div class="service" style="left:118px">
  <div class="photo" role="img" aria-label="Hand typing on a laptop showing a trading chart" style="background:linear-gradient(150deg,#1a1a22 0%,#3a2a30 40%,#7a6a68 75%,#2a2a30 100%)"></div>
  <div class="label">Trading</div>
</div>
<div class="service feature" style="left:445px">
  <svg class="abs" style="left:114px;top:40px" width="82" height="82" viewBox="0 0 82 82" fill="none" stroke="#fff" stroke-width="3">
    <circle cx="41" cy="41" r="22"/><circle cx="41" cy="41" r="8"/>
    <path d="M41 5v10M41 67v10M5 41h10M67 41h10M15 15l7 7M60 60l7 7M15 67l7-7M60 22l7-7"/>
  </svg>
  <h3>Aircraft Finance</h3>
  <p>Lorem ipsum dolor sit amet, consectetur adipiscing elit, sed do eiusmod tempor incididunt ut labore</p>
  <a class="link" href="#">Learn More</a>
</div>
<div class="service" style="left:773px">
  <div class="photo" role="img" aria-label="Warehouse worker holding a tablet among shelves of stock" style="background:linear-gradient(180deg,#c9ccd2 0%,#9aa0a8 45%,#6c7688 75%,#b7a68e 100%)"></div>
  <div class="label">Procurement and Leasing</div>
</div>

<section class="about" role="img" aria-label="Airport apron with parked aircraft at sunset">
  <h2>About Us</h2>
  <p>Founded in 2011, Calder Aviation’s management has many years of experience in Aviation, a strong background in scheduled airlines with emphasis in all cargo operations, freight forwarding supply chain and freight logistics, as well as ACMI and CMI operations. Calder’s focuses in facilitating wet and dry lease operations, charter and ACMI programs consultancy, aircraft sales, leasing and procurement, aviation consultancy and aircraft management.</p>
</section>
<a class="btn btn-dark" style="left:517px;top:1684px;width:166px;height:52px" href="#">Learn More</a>

<h2 class="section-title" style="top:1950px;font-size:34px">Aircraft Available for Sale/Lease</h2>
<p class="avail-text">Sale-leaseback is a method of financing. If your company needs liquidity, your aircraft or engine can serve as collateral for a loan throughout a sale-leaseback transaction. Sale-leaseback can free the equity tied up in aircraft or asset. Even if there is no pressing need for funds, a sale-leaseback allows you to use the equity tied up in your aircraft in a more productive fashion. Leaseback arrangements are usually employed because they confer financing, accounting or taxation benefits.</p>
<a class="btn btn-dark" style="left:517px;top:2170px;width:166px;height:54px" href="#">Learn More</a>

<section class="contact" role="img" aria-label="Aircraft flying over city skyscrapers in a navy tint">
  <h2>Contact Us</h2>
</section>
<div class="field-label" style="left:232px;top:2473px">Tell us your name</div>
<div class="field-label" style="left:620px;top:2473px">Enter your email</div>
<div class="field" style="left:230px;top:2515px;width:351px;height:58px">Enter your name</div>
<div class="field" style="left:618px;top:2515px;width:351px;height:58px">Enter your email</div>
<div class="field-label" style="left:233px;top:2604px">Your website</div>
<div class="field" style="left:232px;top:2646px;width:737px;height:58px">http://</div>
<div class="field-label" style="left:233px;top:2741px">Message</div>
<div class="field area" style="left:232px;top:2782px;width:737px;height:152px">Your message here</div>
<a class="btn btn-light submit" href="#">Submit</a>

<h2 class="section-title" style="top:3195px">Our focus</h2>

<div class="focus" style="left:111px;top:3274px">
  <div class="photo" role="img" aria-label="Glowing world map with connected network points" style="background:radial-gradient(circle at 50% 45%,#4a2a50 0%,#1a2248 55%,#0c1230 100%)"></div>
  <h3>Dry Lease</h3>
  <p style="top:70px">We offer aircraft from our own portfolio on dry lease or could engage in procuring the aircraft of your choice.</p>
  <a class="link" style="top:212px" href="#">Learn More</a>
</div>
<div class="focus" style="left:613px;top:3274px">
  <div class="photo" role="img" aria-label="Model airliner resting on banknotes beside a keyboard" style="background:linear-gradient(160deg,#3a3d45 0%,#9ea3aa 45%,#d8d6cc 70%,#6f7466 100%)"></div>
  <h3>Worldwide Charters</h3>
  <p style="top:70px">We facilitate the arrange-ment of full charters to air-lines and logistics compa-nies. Certain territory restric-tions may apply.</p>
  <a class="link" style="top:212px" href="#">Learn More</a>
</div>
<div class="focus" style="left:111px;top:3555px">
  <div class="photo" role="img" aria-label="Jet airliner flying low over forested hills" style="background:linear-gradient(180deg,#7a93c0 0%,#a9b8d4 45%,#3e4d3a 80%,#1f2a1c 100%)"></div>
  <h3>Asset &amp; Aircraft Management</h3>
  <p style="top:100px">We provide aircraft owners Aircraft Management services, where we manage the techni-cal side of the aircraft.</p>
  <a class="link" style="top:216px" href="#">Learn More</a>
</div>
<div class="focus" style="left:613px;top:3555px">
  <div class="photo" role="img" aria-label="Analyst studying glowing financial data screens" style="background:linear-gradient(120deg,#0c1226 0%,#1d3a66 45%,#2a6a9a 65%,#7a2a3a 85%,#0c1226 100%)"></div>
  <h3>Aviation Consultancy</h3>
  <p style="top:70px">We provide airline consultancy services for new or special projects. Calder also spe-cializes on All Cargo Interna-tional route analysis</p>
  <a class="link" style="top:216px" href="#">Learn More</a>
</div>

<svg class="abs" style="left:0;top:3880px" width="1200" height="150" viewBox="0 3880 1200 150">
  <polygon points="18,4012 600,3892 1182,4012 1168,4020 600,3915 32,4020" fill="var(--silver)"/>
</svg>
<footer class="site-footer"></footer>
<div class="footer-brand"><div class="name">CALDER</div><div class="sub">AVIATION</div></div>
<div class="footer-col">
  <h4 style="left:414px">Customer Support</h4>
  <h4 style="left:703px">Quick Link</h4>
  <h4 style="left:935px">Followers</h4>
</div>
<div class="footer-item" style="left:420px;top:4082px;width:230px">
  <svg width="10" height="14" viewBox="0 0 10 14"><path d="M5 0a5 5 0 0 1 5 5c0 4-5 9-5 9S0 9 0 5a5 5 0 0 1 5-5z" fill="#fff"/><circle cx="5" cy="5" r="2" fill="#000"/></svg>
  <span>Lorem ipsum dolor sit amet<br>consectetur</span>
</div>
<div class="footer-item" style="left:420px;top:4143px">
  <svg width="13" height="13" viewBox="0 0 24 24"><path d="M6.6 10.8a15 15 0 0 0 6.6 6.6l2.2-2.2a1 1 0 0 1 1-.25 11.4 11.4 0 0 0 3.6.57 1 1 0 0 1 1 1V20a1 1 0 0 1-1 1A17 17 0 0 1 3 4a1 1 0 0 1 1-1h3.5a1 1 0 0 1 1 1c0 1.25.2 2.45.57 3.57a1 1 0 0 1-.25 1z" fill="#fff"/></svg>
  <span>188-555-0142</span>
</div>
<div class="footer-item" style="left:704px;top:4082px;flex-direction:column;gap:0">
  <span>&#x276F;&nbsp; Home</span><span>&#x276F;&nbsp; About Us</span><span>&#x276F;&nbsp; Our Services</span><span>&#x276F;&nbsp; Aircraft Available</span><span>&#x276F;&nbsp; Contact Us</span>
</div>
<div class="social" aria-label="Social links"><span></span><span></span><span></span><span></span></div>
<p class="copyright">©Copyrights 2021 Company Name &nbsp;| &nbsp;All Rights Reserved</p>

</body>
</html>
```